Accounting firm needing business card / letterhead designed
Marcus L. Trenholm, CPA
marcus@veltrowledger.com
www.veltrowledger.com
842 E Alder Ave Marrowfield, IA 43827
555-562-0974

```html
<!DOCTYPE html>
<html lang="en">
<head>
<meta charset="utf-8">
<title>Veltrow Ledger – Business Card</title>
<link rel="stylesheet" href="https://fonts.googleapis.com/css2?family=Roboto+Condensed:wght@400;700&display=swap">
<style>
  :root {
    --page-bg: #e7e7e7;
    --card-dark: #2c2d2f;
    --card-green: #62b22f;
    --accent-green: #62b22f;
    --ink-light: #f2f2f2;
    --ink-navy: #2b1f5c;
  }
  * { margin: 0; padding: 0; box-sizing: border-box; }
  html, body {
    width: 1200px; height: 576px; overflow: hidden;
    background: var(--page-bg);
    font-family: "Roboto Condensed", Arial, sans-serif;
  }
  .canvas { position: relative; width: 1200px; height: 576px; }
  .card {
    position: absolute; height: 292px; border-radius: 16px;
    box-shadow: 0 3px 6px rgba(0,0,0,0.18);
  }
  .card--front { left: 82px; top: 139px; width: 484px; background: var(--card-dark); color: var(--ink-light); }
  .card--back { left: 602px; top: 138px; width: 480px; background: var(--card-green); }

  .holder-name {
    position: absolute; left: 29px; top: 38px;
    font-size: 19px; font-weight: 700; letter-spacing: 0.1px;
  }
  .holder-name .credential { color: var(--accent-green); }

  .contact-list { position: absolute; left: 29px; top: 69px; list-style: none; }
  .contact-list li {
    display: flex; align-items: center; height: 15.5px;
    font-size: 12px;
  }
  .contact-list svg { width: 11px; height: 11px; margin-right: 13px; fill: var(--accent-green); }
  .address { position: absolute; left: 29px; top: 119px; font-size: 12px; }

  .wordmark {
    position: absolute; font-weight: 700; font-size: 27px;
    letter-spacing: 1px; text-transform: uppercase; line-height: 1;
  }
  .card--front .wordmark { left: 29px; bottom: 43px; color: var(--ink-light); }
  .card--back .wordmark { right: 30px; bottom: 44px; color: var(--ink-navy); }
</style>
</head>
<body>
<main class="canvas">
  <section class="card card--front" aria-label="Card front">
    <h1 class="holder-name">Marcus L. Trenholm, <span class="credential">CPA</span></h1>
    <ul class="contact-list">
      <li>
        <svg viewBox="0 0 24 24" aria-hidden="true"><path d="M3 8c0-3 4-5 9-5s9 2 9 5v2h-5V8H8v2H3zM6 12h12l2 9H4z"/></svg>
        555-562-0974
      </li>
      <li>
        <svg viewBox="0 0 24 24" aria-hidden="true"><path d="M2 5h20v14H2zM4 7v1l8 5 8-5V7l-8 5z" fill-rule="evenodd"/></svg>
        marcus@veltrowledger.com
      </li>
      <li>
        <svg viewBox="0 0 24 24" aria-hidden="true"><path d="M12 2a10 10 0 1 0 0 20 10 10 0 0 0 0-20zm-1 2.1V11H6.1A8 8 0 0 1 11 4.1zm2 0A8 8 0 0 1 17.9 11H13zM4.1 13H11v6.9A8 8 0 0 1 4.1 13zM13 13h6.9A8 8 0 0 1 13 19.9z"/></svg>
        www.veltrowledger.com
      </li>
    </ul>
    <p class="address">842 E Alder Ave Marrowfield, IA 43827</p>
    <p class="wordmark">Veltrow Ledger</p>
  </section>

  <section class="card card--back" aria-label="Card back">
    <p class="wordmark">Veltrow Ledger</p>
  </section>
</main>
</body>
</html>
```